Web Design Velmora Tech

• An Overview of Velmora Tech for reference: We use to be a component manufacturing company. We sold to customers in USA and manage the builds in China using many manufacturing partners. We had a web site that served this market but we have transitioned over the last several years into “A unique design, development and program management company” It is this message we want to put up on the web now. We provide the design support, we help develop and test a new product for our customers and we provide the manufactured produce once we have transitioned it into production.
• The Target Market: Our customers are all high tech. Each product we produce is custom designed and sold only to one a specific customer. We work with a limited number of customer and sell to new customers by word of mouth and referrals. The web site is to provide a back ground check of any new referral so they can see who we are and our basic capabilities. It is not designed to sell customers or to find new customers but provide a background check to new potential customers.
• Pages Required: We estimate 12:
o Home/Title page is page 1 of PDF. It would have buttons to select other pages
o Names of other pages would be (short titles below if on button, if pull down menu the full title of slide)
 USA Facilities
 China Facilities
 Enclosures
 Antennas
 Connectors
 Cables
 EMI Shields
 Overlays
 Process Development
 BrisaLink
 Contact Us (???) >> new page which we are not sure if we should or should not add.
• Design Specifics; attached is our logo, a PDF and PowerPoint slides showing the views we desire. We like these layouts, but perhaps a better one may be suggested for some artistic reason or layout. It should be clean, simple and user intuitive. We like the off white background and use for most of our presentations. One should be able to go from any screen to any other screen. The quote must include both design and implementation onto our web site which is http://velmoratechworks.example/
• Design Process:
We would like to see concepts of the Landing/Homepage, and an internal page initially. Feedback will be provided and you will be asked to continue if your layout is on the correct track.

• Implementation: Desire designer/implimentor to set up on their server. Allow us to test and edit on their site. We will provide password for implementation on our site after final approval.

Target Market(s)

• The Target Market: see above task descripiton

Industry/Entity Type

It Company

Requirements
Must have
• • Pages Required: We estimate 12:
 USA Facilities
 China Facilities
 Enclosures
 Antennas
 Connectors
 Cables
 EMI Shields
 Overlays
 Process Development
 BrisaLink

Must have the implementation phase include in quote. see task description above
Should not have
• Should not be complex or long time loading.
Do not want any twitter or promotional add on functions.

```html
<!DOCTYPE html>
<html lang="en">
<head>
<meta charset="utf-8">
<title>Velmora Tech – Enclosures</title>
<link href="https://fonts.googleapis.com/css2?family=Source+Sans+3:wght@400;600;700&display=swap" rel="stylesheet">
<style>
  :root{
    --page:#f3f3f1;
    --ink:#4a4a4a;
    --muted:#5c5c5c;
    --blue:#0a6cb6;
    --nav-top:#5a5a5a;
    --nav-bottom:#383838;
    --nav-text:#f2f2f2;
    --frame:#3d3d3d;
    --footer:#e4e4e2;
    --rule:#bdbdbd;
  }
  *{box-sizing:border-box;margin:0;padding:0}
  html,body{width:1200px;height:1121px;overflow:hidden}
  body{background:var(--page);font-family:"Source Sans 3",Arial,sans-serif;color:var(--ink);position:relative}
  .address{position:absolute;top:19px;font-style:normal;font-size:14.5px;line-height:23px;color:var(--muted)}
  .address--usa{right:391px;text-align:right}
  .address--china{left:846px}
  .address-divider{position:absolute;left:829px;top:22px;width:1px;height:38px;background:var(--rule)}

  .brand{position:absolute;left:90px;top:80px;width:208px;height:212px;display:flex;flex-direction:column;align-items:flex-start;justify-content:center;gap:14px}
  .brand-square{width:60px;height:60px;background:var(--blue)}
  .brand-name{font-weight:700;font-size:46px;line-height:46px;color:var(--blue)}

  .main-nav{position:absolute;left:90px;top:300px;width:208px;height:470px;background:linear-gradient(var(--nav-top),var(--nav-bottom));padding-top:7px}
  .main-nav a{display:flex;align-items:center;height:37.6px;padding-left:18px;color:var(--nav-text);text-decoration:none;font-size:14.5px}
  .main-nav a svg{margin-right:15px}
  .main-nav a.is-current{font-weight:600}

  .contact-box{position:absolute;left:90px;top:779px;width:208px;height:220px;background:linear-gradient(var(--nav-top),var(--nav-bottom));color:var(--nav-text);padding:14px 0 0 16px}
  .contact-title{display:flex;align-items:center;gap:8px;margin-left:-6px}
  .contact-title h2{font-size:22px;line-height:27px;font-weight:600}
  .contact-line{font-size:16.5px;font-weight:600;margin-top:12px;color:#e6e6e6}
  .contact-line + .contact-line{margin-top:9px}
  .contact-email{font-size:11.5px;font-weight:600;color:#e6e6e6;margin-top:2px;white-space:nowrap}

  .hero{position:absolute;left:314px;top:80px;width:797px;height:452px;border:3px solid var(--frame);
    background:
      linear-gradient(90deg,rgba(40,40,40,.35) 0%,rgba(0,0,0,0) 25%,rgba(0,0,0,0) 70%,rgba(230,230,230,.35) 100%),
      linear-gradient(180deg,#dcd6cb 0%,#cbc4b7 30%,#6d6a66 55%,#8a6a52 72%,#5c4a3e 100%)}
  .hero-caption{position:absolute;left:0;right:0;bottom:0;height:95px;background:rgba(30,30,30,.82);display:flex;align-items:center;justify-content:space-between;padding:0 24px 0 27px}
  .hero-caption p{color:#fff;font-size:20px;line-height:29px;font-weight:600;width:420px}
  .hero-next{width:30px;height:30px;border-radius:50%;background:#f2f2f2;display:flex;align-items:center;justify-content:center}

  .section-title{position:absolute;left:314px;top:551px;font-size:23px;font-weight:400;color:var(--blue)}
  .body-text{position:absolute;font-size:14.5px;line-height:25px;color:var(--ink);text-align:justify}
  .body-text--intro{left:314px;top:589px;width:558px}
  .sub-title{position:absolute;left:315px;top:757px;font-size:15.5px;font-weight:600;color:var(--blue)}
  .body-text--detail{left:314px;top:785px;width:586px;text-align:left}

  .photo{position:absolute;border:4px solid #fff;box-shadow:0 0 2px rgba(0,0,0,.35)}
  .photo--factory{left:893px;top:595px;width:217px;height:131px;
    background:linear-gradient(180deg,rgba(0,0,0,0) 55%,rgba(200,40,40,.75) 80%,#c2303a 100%),
      linear-gradient(90deg,#b9bcbc 0%,#4f5248 30%,#3c3e3a 50%,#8e9296 75%,#d0802e 100%)}
  .drawing{position:absolute;top:859px;width:183px;height:140px;border:3px solid #d2d2d2;
    background:linear-gradient(135deg,#fdfdfd 0%,#e9e9e9 35%,#f7f7f7 55%,#dedede 80%,#f4f4f4 100%)}
  .drawing--a{left:315px}.drawing--b{left:514px}.drawing--c{left:715px}
  .device{position:absolute;left:923px;top:772px;width:167px;height:230px;
    background:radial-gradient(ellipse at 55% 45%,#3e3f44 0%,#2b2d33 30%,#2a66bf 48%,#1f57b0 75%,rgba(243,243,241,0) 100%)}

  .site-footer{position:absolute;left:0;top:1028px;width:1200px;height:93px;background:var(--footer);text-align:center}
  .footer-nav{margin-top:20px;font-size:14px;color:var(--ink)}
  .footer-nav a{color:var(--ink);text-decoration:none}
  .footer-nav span{margin:0 7px;color:#777}
  .copyright{margin-top:11px;font-size:13.5px;color:var(--ink)}
</style>
</head>
<body>
  <header>
    <address class="address address--usa">48 Orchard Ridge Road, Unit 210<br>Castlebrook, CA - 95190</address>
    <div class="address-divider"></div>
    <address class="address address--china">Lianhe District, Qingshan Lu #27<br>Huayuan, China - 200418</address>
    <div class="brand">
      <div class="brand-square"></div>
      <div class="brand-name">Velmora<br>Tech</div>
    </div>
  </header>

  <nav class="main-nav">
    <a class="is-current" href="#"><svg width="7" height="11" viewBox="0 0 7 11"><polyline points="1,1 5.5,5.5 1,10" fill="none" stroke="#fff" stroke-width="2"/></svg>Home</a>
    <a href="#"><svg width="7" height="11" viewBox="0 0 7 11"><polyline points="1,1 5.5,5.5 1,10" fill="none" stroke="#fff" stroke-width="2"/></svg>USA Facilities</a>
    <a href="#"><svg width="7" height="11" viewBox="0 0 7 11"><polyline points="1,1 5.5,5.5 1,10" fill="none" stroke="#fff" stroke-width="2"/></svg>China Facilities</a>
    <a href="#"><svg width="7" height="11" viewBox="0 0 7 11"><polyline points="1,1 5.5,5.5 1,10" fill="none" stroke="#fff" stroke-width="2"/></svg>Enclosures</a>
    <a href="#"><svg width="7" height="11" viewBox="0 0 7 11"><polyline points="1,1 5.5,5.5 1,10" fill="none" stroke="#fff" stroke-width="2"/></svg>Antennas</a>
    <a href="#"><svg width="7" height="11" viewBox="0 0 7 11"><polyline points="1,1 5.5,5.5 1,10" fill="none" stroke="#fff" stroke-width="2"/></svg>Connectors</a>
    <a href="#"><svg width="7" height="11" viewBox="0 0 7 11"><polyline points="1,1 5.5,5.5 1,10" fill="none" stroke="#fff" stroke-width="2"/></svg>Cables</a>
    <a href="#"><svg width="7" height="11" viewBox="0 0 7 11"><polyline points="1,1 5.5,5.5 1,10" fill="none" stroke="#fff" stroke-width="2"/></svg>EMI Shields</a>
    <a href="#"><svg width="7" height="11" viewBox="0 0 7 11"><polyline points="1,1 5.5,5.5 1,10" fill="none" stroke="#fff" stroke-width="2"/></svg>Overlays</a>
    <a href="#"><svg width="7" height="11" viewBox="0 0 7 11"><polyline points="1,1 5.5,5.5 1,10" fill="none" stroke="#fff" stroke-width="2"/></svg>Process Development</a>
    <a href="#"><svg width="7" height="11" viewBox="0 0 7 11"><polyline points="1,1 5.5,5.5 1,10" fill="none" stroke="#fff" stroke-width="2"/></svg>BrisaLink</a>
    <a href="#"><svg width="7" height="11" viewBox="0 0 7 11"><polyline points="1,1 5.5,5.5 1,10" fill="none" stroke="#fff" stroke-width="2"/></svg>Contact Us</a>
  </nav>

  <aside class="contact-box">
    <div class="contact-title">
      <svg width="46" height="46" viewBox="0 0 46 46">
        <circle cx="23" cy="23" r="22" fill="#f4f4f4"/>
        <circle cx="23" cy="23" r="18" fill="#1e1e1e"/>
        <path d="M16 12c2-1 4 0 5 2l1 4c0 1-1 2-2 2c0 3 2 7 4 9c1-1 2-1 3 0l3 2c1 1 1 3 0 4c-2 2-5 2-7 0c-5-4-8-10-9-16c0-3 0-6 2-7z" fill="#f4f4f4"/>
      </svg>
      <h2>Contact<br>Velmora Tech</h2>
    </div>
    <p class="contact-line">Call us : 555 014 2287</p>
    <p class="contact-line">Fax &nbsp;&nbsp;&nbsp;: 555 014 9631</p>
    <p class="contact-line">Email</p>
    <p class="contact-email">info@velmoratechworks.example</p>
  </aside>

  <main>
    <section class="hero" role="img" aria-label="Photo of three engineers at a table discussing a plastic enclosure prototype in front of a screen showing its 3D model">
      <div class="hero-caption">
        <p>A unique design, development and program management company</p>
        <span class="hero-next"><svg width="10" height="14" viewBox="0 0 10 14"><polyline points="2,1.5 7.5,7 2,12.5" fill="none" stroke="#333" stroke-width="2.6"/></svg></span>
      </div>
    </section>

    <h1 class="section-title">Enclosures</h1>
    <p class="body-text body-text--intro">Morbi porttitor arcu quis sapien porttitor faucibus. Nullam bibendum viverra lorem, luctus suscipit nulla facilisis in. Donec euismod magna quam, quis semper tortor luctus vel. Quisque erat erat, ornare eget pretium eget, hendrerit id magna. Cras dolor quam, faucibus id placerat a, mattis eu elit. Praesent ac lobortis nisl. Integer volutpat tempor eros vitae pulvinar. Praesent nec est iaculis, tincidunt mauris in, vehicula orci. Sed placerat felis risus, ut imperdiet augue adipiscing ac.</p>
    <div class="photo photo--factory" role="img" aria-label="Photo of engineers in hard hats inspecting red enclosure parts on a factory floor"></div>

    <h3 class="sub-title">Mauris aclutus dolo</h3>
    <p class="body-text body-text--detail">Donec euismod magna quam, quis semper tortor luctus vel. Quisque erat erat, ornare eget pre-<br>tium eget, hendrerit id magna. Cras dolor quam, faucibus id placerat a, mattis eu elit.</p>

    <div class="drawing drawing--a" role="img" aria-label="Technical drawing of an enclosure part with views and title block"></div>
    <div class="drawing drawing--b" role="img" aria-label="Technical drawing of an enclosure frame with dimensions"></div>
    <div class="drawing drawing--c" role="img" aria-label="Technical drawing of an enclosure housing in isometric views"></div>
    <div class="device" role="img" aria-label="Photo of a blue handheld electronic device in a custom enclosure"></div>
  </main>

  <footer class="site-footer">
    <nav class="footer-nav">
      <a href="#">Home</a><span>|</span><a href="#">USA Facilities</a><span>|</span><a href="#">China Facilities</a><span>|</span><a href="#">Enclosures</a><span>|</span><a href="#">Antennas</a><span>|</span><a href="#">Connectors</a><span>|</span><a href="#">Cables</a><span>|</span><a href="#">EMI Shields</a><span>|</span><a href="#">Overlays</a><span>|</span><a href="#">Process Development</a><span>|</span><a href="#">BrisaLink</a><span>|</span><a href="#">Contact Us</a>
    </nav>
    <p class="copyright">Copyright © 2013 &nbsp;Velmora Tech. &nbsp;&nbsp;All rights reserved.</p>
  </footer>
</body>
</html>
```